Church Website with Home Page and Member Sermon Library

I am in need of an updated design for our church website. This will include 4 pages (outlined below). We are a conservative, evangelical, Christian church. The site should be modern and clean, while still reflecting our conservative values. I already have a logo for our church, and I want the site to incorporate the logo, and match the logo/branding. Stock photos are allowed if needed, but I have uploaded some images of our church and would prefer those images to be used if possible. Any stock photos used should not include any people in the photos (scenery, nature, buildings, animals, etc. are fine).

The site will need 4 pages: Home, Support Us (Donate), Login, and Recording Library.

Page 1: Home
The home page should include the following sections:

- Navigation: Should include links to each section of the home page plus a "listen live" link which will take the user to a live-streaming site and a "support us" link which will take the user to a support/donate page.

- Announcements: Can be either a banner or some other design, but there needs to be some way for us to post announcements for visitors to see. I'm open for creative ideas in this section, but would like it not to take up a lot of room on the page.

- About Us: Should include address, service times (see attached document), and information about the church.

- Pastor Bio: A section that introduces our pastor and gives a short bio about our pastor. Would like this section to include a picture of our pastor. Somewhere in this section I would like to include this Bible reference: "And I will give you pastors according to mine heart, which shall feed you with knowledge and understanding. Jer 3:15 LPW"

- Articles of Faith (What We Believe): This should include several sub-sections each with a heading, body, and possibly 1 or more scripture references. I have attached a document to the brief that includes our articles of faith. Feel free to be creative with this section in how you lay these out and format them.

- Support Us: A small section that explains what kind of support someone can give and a link to a donation page. The link can say something like "Support Us" or "Donate Now".

- Contact form: A contact form that allows the visitor to send us a message. The contact form should ask for name, email, phone, and message.

- Footer: A footer that will be displayed on all pages of the site. This should include at a minimum a link to the home page (or a link to each individual section in the home page if you prefer), a link to "listen live", a link to "support us", a link to "contact us" (or you can put the contact form directly in the footer if you prefer), the address, and a "member login" link.

Page 2: Support Us
The donation page should include a form the visitor can fill out to make a donation. We will embed a third party form later. For this design, please just mock out the design with a basic form asking for name, phone, and email.

Page 3: Login
The recording library (detailed below) will require members to login with a shared numeric code before accessing the page. We need a design for a login screen. The screen should include navigation/footer just like all other pages, but the body of the login page will consist only of a form that asks the user to enter the access code and then a "login" button.

Page 4: Recording Library

The library page is a member-only page that will require a shared, numeric pass code to access. On this page, members will be able to access a filterable list of past sermons. The page by default should display most recent sermons, but should also include a search form that allows the member to filter the sermon list to find a particular sermon. The search form should allow the user to select a filter type (e.g. Speaker name, date, event, etc.) and type in a value to search. They should be able to add multiple filters and remove filters that have been added. Each sermon that is displayed in the result list should include basic information such as title, date, speaker, tags, etc. along with a download icon, and an embedded audio player where they can click a play button to stream it on-demand. Each sermon should also have clickable tags associated with it that can be used to find related sermons.
Updates

I have uploaded several images of our church. Feel free to incorporate these into your design if possible.

Target Market(s)

Church Members

Industry/Entity Type

Religion

Number of Pages Required

4 page

Font styles to use
Sans Serif

Colors

Designer to choose colors to be used in the design.

Requirements
Must have
• Must incorporate the logo (attached)
Nice to have
• Would like the design to incorporate pictures of our church (attached) instead of stock photos if possible.
Should not have
• Please avoid an overly cluttered design. Stock photos used should not include any people in the photos.

```html
<!DOCTYPE html>
<html lang="en">
<head>
<meta charset="utf-8">
<title>Cedar Hill Church – Website Design</title>
<link href="https://fonts.googleapis.com/css2?family=Tinos:wght@400;700&family=Arimo:wght@400;700&display=swap" rel="stylesheet">
<style>
:root{
  --teal:#0b7d8e;
  --teal-dark:#0c6f7a;
  --ink:#222;
  --muted:#555;
  --dark:#333;
  --green:#1f8a1f;
  --cyan:#17c3de;
  --panel:#f2f2f2;
  --line:#d6d6d6;
  --lib-head:#d3e8da;
  --lib-text:#1d6b3a;
}
*{box-sizing:border-box;margin:0;padding:0}
html,body{width:1200px;height:1200px;overflow:hidden;background:#fff}
.canvas{position:relative;width:1200px;height:1200px;overflow:hidden;font-family:"Tinos",serif;color:var(--ink)}
.abs{position:absolute}
.center{text-align:center}

/* home page */
.site-header{left:176px;top:7px;width:459px;height:34px;background:var(--teal);color:#fff}
.brand{left:10px;top:8px;font-size:8px;letter-spacing:1.5px;color:#fff;font-family:"Tinos",serif}
.brand-mark{display:inline-block;width:6px;height:6px;border:1px solid #fff;margin-right:3px;vertical-align:middle}
.nav a{position:absolute;top:14px;font-size:4.5px;color:#fff;text-decoration:none}
.hero{left:176px;top:41px;width:459px;height:185px;background:linear-gradient(135deg,#a77d65 0%,#8d5f48 45%,#c9c3bd 100%)}
.inset{border:1px solid #fff;background:linear-gradient(160deg,#e7e7e4,#9a8f86)}
.banner-stripe{left:294px;top:141px;width:341px;height:11px;background:linear-gradient(90deg,rgba(230,140,30,0),#e58a1e 20%,#d8661c 70%,#c24a22)}
.banner-text{left:294px;top:142px;width:341px;font-size:9px;font-weight:700;color:#fff;text-align:center}
.btn-green{background:var(--green);color:#fff;font-size:5px;text-align:center;border-radius:2px;line-height:12px;width:58px;height:12px}
.info-title{left:176px;top:239px;width:459px;font-size:9.5px;color:var(--teal)}
.info-text{left:176px;top:255px;width:459px;font-size:4.3px;color:var(--teal)}
.rule{height:0;border-top:1px solid var(--line)}
.about-band{left:172px;top:294px;width:463px;height:70px;background:var(--teal);color:#fff}
.about-band h2{position:absolute;left:0;top:8px;width:100%;font-size:9.5px;font-weight:400;text-align:center}
.about-col{position:absolute;top:23px;width:120px;text-align:center;font-size:4.8px;line-height:8.3px}
.about-col .head{font-size:9px;line-height:11px}
.about-col .name{font-size:6px}
.times-title{left:176px;top:371px;width:459px;font-size:9.5px;color:var(--teal)}
.time-item{top:386px;width:90px;font-size:6px;color:var(--teal);text-align:center;line-height:8.5px}
.time-item small{display:block;font-size:5px;margin-top:2px}
.tick{display:inline-block;width:6px;height:6px;border-radius:50%;background:var(--teal);vertical-align:-1px;margin-right:2px;position:relative}
.pastors-title{left:176px;top:429px;width:459px;font-size:9px;font-weight:700}
.pastors-quote{left:176px;top:444px;width:459px;font-size:5.8px}
.pastor-card{top:455px;width:123px;height:83px;border:1px solid #bbb;background:linear-gradient(180deg,#f5f5f5,#cfcfcf)}
.pastor-name{top:541px;width:123px;font-size:6px;font-weight:700;text-align:center}
.pastor-bio{top:552px;width:123px;font-size:4.5px;line-height:8.3px;color:var(--teal);text-align:center}
.beliefs{left:169px;top:573px;width:464px;height:243px;background:var(--dark);color:#fff}
.beliefs h2{position:absolute;left:0;top:9px;width:100%;font-size:8.5px;text-align:center}
.beliefs h3{position:absolute;left:0;top:23px;width:100%;font-size:8.5px;font-weight:400;text-align:center}
.belief-col{position:absolute;top:37px;width:188px;text-align:center;font-size:4.5px;line-height:8.3px;color:#ddd}
.belief-col h4{font-size:6px;color:#fff;margin-bottom:2px}
.belief-col p{margin-bottom:4px}
.belief-col .ref{color:#555;margin-bottom:6px}
.belief-col b{color:#fff}
.faith-band{left:169px;top:819px;width:464px;height:112px;background:var(--teal);color:#fff}
.faith-col{position:absolute;top:10px;font-size:6.3px;line-height:8.3px}
.faith-col h4{font-size:9px;text-align:center;margin-bottom:3px}
.contact-title{left:169px;top:942px;width:464px;font-size:13px;text-align:center;border-top:1px solid #eee;padding-top:2px}
.plant{left:197px;top:975px;width:109px;height:125px;background:radial-gradient(ellipse at 40% 50%,rgba(120,160,90,.55),rgba(190,215,170,.25) 55%,rgba(255,255,255,0) 75%)}
.contact-lead{left:197px;top:982px;width:196px;font-size:9px}
.contact-note{left:197px;top:995px;width:196px;font-size:6px;line-height:8.3px;color:var(--teal)}
.field-label{font-size:4.8px}
.field{border:1px solid #ccc;height:12px;font-size:4.8px;color:#888;padding:3px 4px;width:189px;background:#fff}
.textarea{border:1px solid #aaa;background:#eef9fb;width:186px;height:69px}
.send{left:411px;top:1129px;width:48px;height:12px;background:var(--teal-dark);color:#fff;font-size:5px;text-align:center;line-height:12px}

/* account forms */
.forms-panel{left:672px;top:7px;width:464px;height:712px;background:var(--panel)}
.form-card{background:#fff;border:1px solid #e0e0e0;border-radius:3px;font-family:"Arimo",sans-serif}
.card-brand{position:absolute;left:0;top:16px;width:100%;text-align:center;font-family:"Tinos",serif;font-size:7px;letter-spacing:1.5px;color:#2a9d9a}
.card-title{position:absolute;left:4px;font-size:6.5px;color:#222}
.card-input{position:absolute;left:4px;height:12px;border:1px solid #ddd;border-radius:2px;font-size:5px;color:#888;padding:3px 4px}
.card-btn{position:absolute;left:4px;height:13px;background:var(--cyan);color:#fff;font-size:5px;text-align:center;line-height:13px;border-radius:2px}
.card-link{position:absolute;left:4px;font-size:4.3px}
.card-link a{color:#2a6fd6}

/* recording library */
.lib{font-family:"Arimo",sans-serif}
.lib-head{left:737px;top:762px;width:387px;height:26px;background:var(--lib-head);border:1px solid #c6dccd;color:var(--lib-text);font-size:11px;text-align:center;line-height:26px}
.lib-label{font-size:4.5px}
.lib-input{border:1px solid #ccc;border-radius:2px;font-size:5px;color:#888;padding:2px 4px;background:#fff}
.lib-btn{font-size:5px;color:#fff;text-align:center;line-height:13px;border-radius:2px;height:13px}
.date-panel{left:934px;top:796px;width:77px;height:73px;border:1px solid #cfe0ee;background:#fff}
.date-head{height:20px;background:#e7f1fb;font-size:5px;color:#2a6fd6;padding:7px 7px}
.lib-table{left:737px;top:873px;width:387px;font-size:4.8px;border-collapse:collapse}
.lib-table th{background:#d6d6d6;font-weight:700;text-align:left;vertical-align:bottom;padding:3px 2px;height:22px}
.lib-table td{background:#f2f2f2;vertical-align:top;padding:3px 2px;height:23px;line-height:8px}
.lib-table a{color:#2a6fd6}
.play{display:inline-block;width:9px;height:9px;background:#1a73e8;border-radius:1px;vertical-align:middle;position:relative}

/* footer */
.site-footer{left:694px;top:967px;width:463px;height:84px;background:var(--teal-dark);color:#fff;font-size:4.5px}
.footer-rule{left:694px;top:1057px;width:463px;border-top:1px solid #888}
.social{width:6px;height:6px;border-radius:50%;background:#fff}
</style>
</head>
<body>
<div class="canvas">

  <!-- HOME PAGE -->
  <header class="abs site-header">
    <div class="abs brand"><span class="brand-mark"></span>CEDAR HILL</div>
    <nav class="nav">
      <a style="left:306px">Home</a>
      <a style="left:347px">Support Us</a>
      <a style="left:387px">
        <svg width="5" height="5" viewBox="0 0 10 10" style="vertical-align:-1px"><circle cx="5" cy="3" r="2.5" fill="#fff"/><path d="M0 10c0-3 2-4.5 5-4.5s5 1.5 5 4.5z" fill="#fff"/></svg>
        &nbsp;Login</a>
      <a style="left:418px">Recording Library</a>
    </nav>
  </header>

  <section class="abs hero" role="img" aria-label="Photo of the brick church front with its service sign"></section>
  <div class="abs inset" style="left:195px;top:102px;width:86px;height:86px" role="img" aria-label="Photo of the church building in winter"></div>
  <div class="abs inset" style="left:231px;top:136px;width:69px;height:69px" role="img" aria-label="Photo of the church from the road"></div>
  <div class="abs banner-stripe"></div>
  <div class="abs banner-text">WE LOVE BECAUSE HE FIRST LOVE US</div>
  <div class="abs btn-green" style="left:449px;top:169px">Listen Live</div>
  <div class="abs btn-green" style="left:449px;top:186px">Support Us</div>

  <h2 class="abs info-title center" style="font-weight:400">Information</h2>
  <p class="abs info-text center">This information will appear in the system, taken from the database and only the admin can input this information data, the admin can edit to mark the active status</p>
  <div class="abs rule" style="left:208px;top:268px;width:395px"></div>

  <section class="abs about-band">
    <h2>About Us</h2>
    <div class="about-col" style="left:40px">
      <div class="name">Cedar Hill Church</div>
      <div>
        <svg width="6" height="4" viewBox="0 0 12 8"><path d="M0 1l4-1 4 1 4-1v7l-4 1-4-1-4 1z" fill="#fff"/></svg>
        &nbsp;Address</div>
      <div>Lorem ipsum</div><div>Lorem ipsum</div><div>Lorem ipsum</div>
    </div>
    <div class="about-col" style="left:169px">
      <div class="head">
        <svg width="6" height="6" viewBox="0 0 10 10"><path d="M2 0l2 2.5-1.2 1.3c.7 1.5 1.9 2.7 3.4 3.4L7.5 6 10 8l-1.5 2C4 10 0 6 0 1.5z" fill="#fff"/></svg>
        Phone</div>
      <div>Lorem ipsum</div><div>Lorem ipsum</div><div>Lorem ipsum</div>
    </div>
    <div class="about-col" style="left:298px">
      <div class="head">E-mail</div>
      <div>Lorem ipsum</div><div>Lorem ipsum</div><div>Lorem ipsum</div>
    </div>
  </section>

  <h2 class="abs times-title center" style="font-weight:400">
    <svg width="8" height="8" viewBox="0 0 10 10" style="vertical-align:-1px"><circle cx="5" cy="5" r="5" fill="var(--teal)"/><path d="M5 2v3.2l2 1.3" stroke="#fff" stroke-width="1.2" fill="none"/></svg>
    Regular Service Times :</h2>
  <div class="abs time-item" style="left:211px"><span class="tick"></span>Wednesday Evening Service:<small>7:30 PM</small></div>
  <div class="abs time-item" style="left:308px"><span class="tick"></span>Sunday School:<small>10:00 AM</small></div>
  <div class="abs time-item" style="left:405px"><span class="tick"></span>Sunday Morning Service:<small>11:00 AM</small></div>
  <div class="abs time-item" style="left:502px"><span class="tick"></span>Sunday Evening Service:<small>5:30 PM</small></div>
  <div class="abs rule" style="left:208px;top:418px;width:395px"></div>

  <h2 class="abs pastors-title center">Our Pastors</h2>
  <p class="abs pastors-quote center">"And I will give you pastors according to mine heart, which shall feed you with knowledge and understanding. Jer 3:15 LPW"</p>
  <div class="abs pastor-card" style="left:211px" role="img" aria-label="Portrait of a pastor"></div>
  <div class="abs pastor-card" style="left:342px" role="img" aria-label="Portrait of a pastor"></div>
  <div class="abs pastor-card" style="left:474px" role="img" aria-label="Portrait of a pastor"></div>
  <div class="abs pastor-name" style="left:211px">Name</div>
  <div class="abs pastor-name" style="left:342px">Name</div>
  <div class="abs pastor-name" style="left:474px">Name</div>
  <p class="abs pastor-bio" style="left:211px">Loren ipsum Loren ipsum Loren ipsum Loren ipsum Loren ipsum Loren ipsum Loren ipsum</p>
  <p class="abs pastor-bio" style="left:342px">Loren ipsum Loren ipsum Loren ipsum Loren ipsum Loren ipsum Loren ipsum Loren ipsum</p>
  <p class="abs pastor-bio" style="left:474px">Loren ipsum Loren ipsum Loren ipsum Loren ipsum Loren ipsum Loren ipsum Loren ipsum</p>

  <section class="abs beliefs">
    <h2>What We Believe</h2>
    <h3>Statemens Of Faith</h3>
    <div class="belief-col" style="left:40px">
      <h4>The God Head.</h4>
      <p>We believe in the God head bodily, known as the Divine Trinity. This body consist of God the father, Jesus Christ, his only begotten son and the redeemer of the world, and of the Holy Ghost, The third person of the Divine Trinity.</p>
      <h4 style="margin-top:6px">Full Salvation.</h4>
      <p>We believe that Salvation is received only when a person comes to the realization that he or she is lost and separated from God and becomes full of godly sorrow, confessing their sins and true repentance, believing in the shed blood of the Lord Jesus Christ as the only sacrifice for sins. Through the blood of Christ we have:</p>
      <p><b>(1) remission of sins, Matthew 26:28 Heb 9:22<br>(2) Sanctification. Hebrews 13:12<br>(3) redemption. Revelations 5:9<br>(4) cleansing. 1 John 1:7 Rev. 1:5<br>(5). Justification. Romans 5:9</b></p>
      <h4 style="margin-top:14px">Second coming of Christ.</h4>
      <p>We believe in the second coming of Jesus Christ.</p>
      <p class="ref">Matthew 24:44 Luke 12:40</p>
    </div>
    <div class="belief-col" style="left:238px">
      <h4>Sanctification</h4>
      <p>"Sanctify them through thy truth thy word is truth St John 17:17. For this is the will of God even your sanctification"<br>We believe in a set apart life, separate from the world to Christ</p>
      <p class="ref">2 Cor 6:17-18</p>
      <h4>Baptism of the Holy Ghost</h4>
      <p>We believe in the baptism of the Holy Ghost as it is taught in the Bible and promised by our Lord Jesus Christ, with speaking in tongues as the Spirit gives utterance as the initial evidence. Acts 2:4 we believe that the gift of the Holy Ghost is for all believers as the Lord promised.</p>
      <p class="ref">Acts 2:17-18</p>
      <h4>Divine Healing.</h4>
      <p>We believe Divine Healing to be included in the atonement of Jesus Christ our Lord, And believe that it is still for us today.</p>
      <p class="ref">1 Peter 2:24 Luke 9:1-2 Mark 16:18 James 5:15</p>
      <h4>Eternity</h4>
      <p>We believe in Literal Eternity. Eternal Life for the believer and eternal death for those without Christ.</p>
      <p class="ref">Revelation 20:15</p>
    </div>
  </section>

  <section class="abs faith-band">
    <div class="faith-col" style="left:40px;width:182px">
      <h4>Sanctification</h4>
      <p>“Sanctify them through thy truth thy word is truth St John 17:17. For this is the will of God even your sanctification”<br>We believe in a set apart life, separate from the world to Christ 2 Cor 6:17-18</p>
    </div>
    <div class="faith-col" style="left:238px;width:189px">
      <h4>Baptism of the Holy Ghost</h4>
      <p>We believe in the baptism of the Holy Ghost as it is taught in the Bible and promised by our Lord Jesus Christ, with speaking in tongues as the Spirit gives utterance as the initial evidence. Acts 2:4 we believe that the gift of the Holy Ghost is for all believers as the Lord promised. Acts 2:17-18 Divine Healing.<br>We believe Divine Healing to be included in the atonement of Jesus Christ our Lord, And believe that it is still for us today. 1 Peter 2:24 Luke 9:1-2 Mark 16-18 James 5:15</p>
    </div>
  </section>

  <h2 class="abs contact-title" style="font-weight:400">Contact Us</h2>
  <div class="abs plant" role="img" aria-label="Illustration of leafy plants and daisies on stones"></div>
  <p class="abs contact-lead">We Would Love to Hear from You!</p>
  <p class="abs contact-note">Please write or call us with your questions or comments. We would also love to receive your prayer requests!</p>

  <form class="contact-form">
    <label class="abs field-label" style="left:411px;top:971px">Name:</label>
    <div class="abs field" style="left:411px;top:979px">Name</div>
    <label class="abs field-label" style="left:411px;top:993px">Email:</label>
    <div class="abs field" style="left:411px;top:1001px">Email</div>
    <label class="abs field-label" style="left:411px;top:1014px">Phone:</label>
    <div class="abs field" style="left:411px;top:1022px">Phone</div>
    <label class="abs field-label" style="left:411px;top:1044px">Message:</label>
    <div class="abs textarea" style="left:411px;top:1056px"></div>
    <div class="abs send">Send</div>
  </form>

  <!-- ACCOUNT FORMS -->
  <div class="abs forms-panel"></div>
  <div class="abs rule" style="left:672px;top:483px;width:464px;border-color:#bbb"></div>

  <div class="abs form-card" style="left:839px;top:31px;width:139px;height:138px">
    <div class="card-brand">CEDAR HILL</div>
    <div class="card-title" style="top:35px">Login</div>
    <div class="card-input" style="top:53px;width:130px">Name or Email</div>
    <div class="card-input" style="top:74px;width:130px">Password</div>
    <div class="card-btn" style="top:93px;width:70px">Login</div>
    <div class="card-link" style="top:114px">Don't have account ? <a>Registration</a></div>
  </div>

  <div class="abs form-card" style="left:839px;top:267px;width:139px;height:156px">
    <div class="card-brand">CEDAR HILL</div>
    <div class="card-title" style="top:35px">Registration</div>
    <div class="card-input" style="top:53px;width:130px">name</div>
    <div class="card-input" style="top:74px;width:130px">Password</div>
    <div class="card-input" style="top:94px;width:130px">Retype Password</div>
    <div class="card-btn" style="top:114px;width:70px">Register</div>
    <div class="card-link" style="top:136px"><a>Log In</a></div>
  </div>

  <div class="abs form-card" style="left:836px;top:508px;width:135px;height:151px">
    <div class="card-brand">CEDAR HILL</div>
    <div class="card-title" style="top:37px">Change Password</div>
    <div class="card-input" style="top:52px;width:127px">Old password</div>
    <div class="card-btn" style="top:71px;width:68px">Submit</div>
    <div class="card-input" style="top:92px;width:127px">New Password</div>
    <div class="card-input" style="top:112px;width:127px">Retype New Password</div>
    <div class="card-btn" style="top:132px;width:68px">Change Password</div>
  </div>

  <!-- RECORDING LIBRARY -->
  <section class="lib">
    <h2 class="abs lib-head" style="font-weight:400">Recording Library</h2>
    <div class="abs lib-label" style="left:737px;top:798px">Search</div>
    <div class="abs lib-input" style="left:737px;top:809px;width:189px;height:13px;color:#222">p</div>
    <div class="abs lib-label" style="left:737px;top:824px">Event</div>
    <div class="abs lib-input" style="left:737px;top:830px;width:189px;height:13px">Input event</div>
    <div class="abs lib-btn" style="left:737px;top:851px;width:26px;background:#1a6fd6;outline:1px solid #7aa8ec">Submit</div>
    <div class="abs lib-btn" style="left:765px;top:851px;width:21px;background:var(--cyan);color:#222">Clear</div>
    <div class="abs date-panel">
      <div class="date-head">Date
        <svg width="6" height="4" viewBox="0 0 10 6" style="float:right;margin-top:1px"><path d="M1 5l4-4 4 4" stroke="#2a6fd6" fill="none"/></svg>
      </div>
      <div class="abs lib-label" style="left:7px;top:28px">From</div>
      <div class="abs lib-input" style="left:7px;top:33px;width:69px;height:14px;color:#222">mm/dd/yyyy</div>
      <div class="abs lib-label" style="left:7px;top:54px">To</div>
      <div class="abs lib-input" style="left:7px;top:59px;width:69px;height:14px;color:#222">mm/dd/yyyy</div>
    </div>
    <table class="abs lib-table">
      <tr>
        <th style="width:8px">#</th><th style="width:44px">Speaker Name</th><th style="width:139px">Sort Description</th>
        <th style="width:44px">Date of sermon</th><th style="width:55px">Tags</th><th style="width:57px">Videos</th><th>Length Audio</th>
      </tr>
      <tr>
        <td>1</td><td>Pastor Mark Ellis</td><td>How to deal with depression due to pressure from outsiders</td>
        <td>2023-02-07</td><td><a>http://www.samplelink.org</a></td>
        <td><a>test.mp4</a> <span class="play"><svg width="9" height="9" viewBox="0 0 10 10"><path d="M3 2l5 3-5 3z" fill="#fff"/></svg></span></td>
        <td>5</td>
      </tr>
    </table>
  </section>

  <!-- FOOTER -->
  <footer class="abs site-footer">
    <div class="abs" style="left:47px;top:29px;font-size:8px;letter-spacing:1.5px">CEDAR HILL</div>
    <div class="abs center" style="left:198px;top:6px;width:70px;font-weight:700">Cedar Hill Church</div>
    <div class="abs center" style="left:198px;top:14px;width:70px;font-size:4px">Address</div>
    <div class="abs" style="left:218px;top:25px;width:30px;border-top:1px solid #fff"></div>
    <div class="abs" style="left:217px;top:31px;font-size:4px">
      <svg width="5" height="5" viewBox="0 0 10 10"><path d="M2 0l2 2.5-1.2 1.3c.7 1.5 1.9 2.7 3.4 3.4L7.5 6 10 8l-1.5 2C4 10 0 6 0 1.5z" fill="#fff"/></svg> ___ ____</div>
    <div class="abs center" style="left:287px;top:6px;width:50px;line-height:8.3px">
      <b>Menu</b><br>About Us<br>Donation<br>Listen Live<br>About Us<br>Contact Us
    </div>
    <div class="abs social" style="left:378px;top:7px"></div>
    <div class="abs social" style="left:389px;top:7px"></div>
    <div class="abs social" style="left:400px;top:7px"></div>
    <div class="abs" style="left:40px;top:73px;font-size:3.8px;font-weight:700">© Cedar Hill Church | 2023 | All Rights Reserved</div>
  </footer>
  <div class="abs footer-rule"></div>

</div>
</body>
</html>
```